Business Card for Industrial Distributor

We need a business card design for an industrial distributor. We sell machine parts for the manufacturing and oil industry. We would like the cards to look clean and modern but with a touch of industry.

Our colors are blue/white.

Please feel free to visit our website www.korvelpartsco.com

Target Market(s)

mexican manufacturers in the automobile/aerospace industry

Industry/Entity Type

Industrial

Colors
ffffff
0555a3

```html
<!DOCTYPE html>
<html lang="en">
<head>
<meta charset="utf-8">
<title>Korvel Business Card</title>
<link rel="stylesheet" href="https://fonts.googleapis.com/css2?family=Exo+2:wght@600&family=Open+Sans:wght@400;700&display=swap">
<style>
  :root {
    --page-bg: #e9e6e1;
    --card-front: #0b0b0c;
    --card-back: #ffffff;
    --brand-blue: #2a3a9c;
    --ink: #1d1d1f;
    --icon: #2b2b2b;
  }
  * { margin: 0; padding: 0; box-sizing: border-box; }
  html, body { width: 1200px; height: 900px; overflow: hidden; }
  body {
    background: var(--page-bg);
    font-family: "Open Sans", sans-serif;
    position: relative;
  }
  .card {
    position: absolute;
    width: 600px;
    height: 343px;
    box-shadow: 0 10px 28px rgba(0,0,0,.18);
  }
  .card--front {
    left: 60px; top: 90px;
    background: var(--card-front);
    display: flex; align-items: center; justify-content: center;
  }
  .card--back {
    left: 540px; top: 460px;
    background: var(--card-back);
  }
  .wordmark {
    display: flex; align-items: center; gap: 16px;
  }
  .wordmark__dot {
    width: 72px; height: 72px; border-radius: 50%;
    background: var(--brand-blue);
  }
  .wordmark__name {
    font-family: "Open Sans", sans-serif;
    font-weight: 700;
    color: var(--brand-blue);
    font-size: 68px;
    line-height: 1;
    letter-spacing: 1px;
  }
  .contact {
    position: absolute; left: 210px; top: 24px;
  }
  .contact__name {
    font-family: "Exo 2", sans-serif;
    font-weight: 600;
    font-size: 27px;
    color: var(--brand-blue);
    line-height: 1.05;
  }
  .contact__title {
    font-size: 13px; color: var(--ink); margin-left: 8px;
  }
  .contact__list {
    list-style: none; margin: 14px 0 0 26px;
  }
  .contact__item {
    display: flex; align-items: center; gap: 8px;
    font-size: 14px; color: var(--ink); line-height: 20px;
  }
  .contact__item svg { width: 11px; height: 11px; fill: var(--icon); flex: none; }
  .contact__address {
    font-size: 14px; color: var(--ink); line-height: 20px;
    margin: 10px 0 0 26px;
  }
  .card--back .wordmark {
    position: absolute; left: 40px; bottom: 22px;
  }
  .card--back .wordmark__dot { width: 78px; height: 78px; }
</style>
</head>
<body>
  <section class="card card--front" aria-label="Card front">
    <div class="wordmark">
      <span class="wordmark__dot"></span>
      <span class="wordmark__name">Korvel</span>
    </div>
  </section>

  <section class="card card--back" aria-label="Card back">
    <div class="contact">
      <h1 class="contact__name">Daniel Harper</h1>
      <p class="contact__title">Managing Director</p>
      <ul class="contact__list">
        <li class="contact__item">
          <svg viewBox="0 0 12 12"><path d="M1 4c0-2 2-3 5-3s5 1 5 3H8.5V3h-5v1zM2.5 5h7l1.5 5H1z"/></svg>
          (044) 123 456 789
        </li>
        <li class="contact__item">
          <svg viewBox="0 0 12 12"><path d="M3.5 0h5a1 1 0 0 1 1 1v10a1 1 0 0 1-1 1h-5a1 1 0 0 1-1-1V1a1 1 0 0 1 1-1zm.5 1.5v8h4v-8z"/></svg>
          (044)123456789
        </li>
        <li class="contact__item">
          <svg viewBox="0 0 12 12"><path d="M0 2h12v8H0zm1 1v.4l5 3.3 5-3.3V3z"/></svg>
          info@youremail.com
        </li>
        <li class="contact__item">
          <svg viewBox="0 0 12 12"><circle cx="6" cy="6" r="5.5"/></svg>
          www.webname.com
        </li>
      </ul>
      <p class="contact__address">12345,your address goes here,<br>country name,12345</p>
    </div>
    <div class="wordmark">
      <span class="wordmark__dot"></span>
      <span class="wordmark__name">Korvel</span>
    </div>
  </section>
</body>
</html>
```